Car Detailing Brochure/PriceList

Looking for a nicely designed Brochure/Price sheet that can be displayed on the website and Murmurly sites which details the different service stages available to potential customers

Target Market(s)

People in the local area who need paint enhancement and correction

Industry/Entity Type

Car Detailing

Requirements
Must have
• Reader Friendly, Informative, pictures (lots on Murmurly/Website that can be used) would like to see nicely imbedded pictures relating to stages etc
Nice to have
• Luxury design following company branding with logo/colours etc https://www.velvorashine.uk/services

```html
<!DOCTYPE html>
<html lang="en">
<head>
<meta charset="utf-8">
<title>Velvora Shine – Detailing Stages &amp; Prices</title>
<link rel="stylesheet" href="https://fonts.googleapis.com/css2?family=Montserrat:ital,wght@0,500;0,600;0,700;0,800;1,500&family=Anton&display=swap">
<style>
  :root{
    --dark:#231f20;
    --yellow:#fdb913;
    --orange:#f26306;
    --red:#ed1c24;
    --brown:#3d1d0a;
    --white:#ffffff;
    --ink:#111111;
    --green:#3cc84a;
    --pin:#f7941d;
    --soft:#d7d8da;
  }
  *{margin:0;padding:0;box-sizing:border-box}
  html,body{width:927px;height:1200px;overflow:hidden;background:var(--white)}
  body{font-family:"Montserrat",sans-serif;color:var(--white)}
  .sheet{position:relative;width:927px;height:1200px;overflow:hidden;
    background:linear-gradient(90deg,#c9cacc 0%,#f4f4f5 45%,#f4f4f5 60%,#c6c7c9 100%)}
  .shapes{position:absolute;left:0;top:0;width:927px;height:1200px}
  .abs{position:absolute}

  .brand{left:60px;top:44px;color:var(--ink)}
  .brand-name{font-weight:800;font-size:24px;letter-spacing:0.5px;line-height:1;display:flex;align-items:center;gap:6px}
  .brand-dot{width:10px;height:10px;border-radius:50%;background:var(--ink);display:inline-block}
  .brand-tag{font-weight:600;font-size:7.6px;letter-spacing:0.6px;color:var(--white);margin-top:5px;text-shadow:0 0 1px #777}

  .stage-title{font-weight:800;font-size:39px;line-height:1;color:var(--yellow);letter-spacing:0.5px;white-space:nowrap}
  .stage-copy{font-weight:500;font-size:11.2px;line-height:13.25px;letter-spacing:-0.3px;white-space:nowrap}
  .right{text-align:right}

  .prices-label{font-weight:500;font-size:13.5px;line-height:1;white-space:nowrap}
  .price-col{font-weight:600;font-size:9.4px;line-height:12px;white-space:nowrap}
  .footnote{font-style:italic;font-weight:500;font-size:6.6px;line-height:1;white-space:nowrap}

  .upgrades{left:29px;top:1059px;width:318px}
  .upgrades h2{font-weight:600;font-size:15.4px;line-height:1;margin-bottom:8px;white-space:nowrap}
  .upgrade-list{list-style:none}
  .upgrade-list li{display:flex;align-items:baseline;font-weight:500;font-size:10.8px;line-height:13.7px;white-space:nowrap}
  .upgrade-list .lead{flex:1;border-bottom:1px dashed rgba(255,255,255,.85);margin:0 4px;transform:translateY(-3px)}
  .upgrade-list .two{display:block}

  .footer-brand{left:393px;top:1066px;color:var(--ink)}
  .footer-brand .brand-name{font-size:13px;gap:4px}
  .footer-brand .brand-dot{width:6px;height:6px}
  .footer-brand .brand-tag{font-size:4.2px;margin-top:2px;color:var(--ink);text-shadow:none;letter-spacing:0.2px}

  .call-icon{left:393px;top:1107px;width:30px;height:30px;border-radius:6px;background:var(--green)}
  .call-label{left:435px;top:1104px;font-family:"Anton",sans-serif;font-size:25px;line-height:1;letter-spacing:0.8px;white-space:nowrap}
  .call-number{left:392px;top:1143px;font-family:"Anton",sans-serif;font-size:31px;line-height:1;letter-spacing:1px;white-space:nowrap}

  .contact{left:596px;top:1103px}
  .contact li{list-style:none;display:flex;align-items:center;height:27px;font-weight:500;font-size:13.4px;white-space:nowrap}
  .contact li.mail{font-size:16.6px}
  .contact .ico{width:16px;display:flex;justify-content:center;margin-right:10px}
  .social-square{width:12px;height:12px;border-radius:2px;background:var(--white)}
</style>
</head>
<body>
<main class="sheet">

  <svg class="shapes" viewBox="0 0 1688 2184" preserveAspectRatio="none" aria-hidden="false">
    <defs>
      <linearGradient id="photoWhiteCar" x1="0" y1="0" x2="1" y2="1">
        <stop offset="0" stop-color="#7d7f82"/>
        <stop offset="0.45" stop-color="#e6e6e4"/>
        <stop offset="0.75" stop-color="#b9babd"/>
        <stop offset="1" stop-color="#2e3033"/>
      </linearGradient>
      <linearGradient id="photoSilverCar" x1="0" y1="0" x2="1" y2="1">
        <stop offset="0" stop-color="#9a9a97"/>
        <stop offset="0.4" stop-color="#d8d5cd"/>
        <stop offset="0.7" stop-color="#a9a7a2"/>
        <stop offset="1" stop-color="#3e3e3e"/>
      </linearGradient>
      <linearGradient id="photoBlackCar" x1="0" y1="0" x2="1" y2="1">
        <stop offset="0" stop-color="#2a2a2c"/>
        <stop offset="0.45" stop-color="#0f0f10"/>
        <stop offset="0.75" stop-color="#4a4a4e"/>
        <stop offset="1" stop-color="#c4c5ca"/>
      </linearGradient>
    </defs>

    <!-- stage one -->
    <rect x="73" y="187" width="1541" height="438" fill="var(--dark)"/>
    <rect x="1000" y="132" width="614" height="55" fill="var(--orange)"/>
    <rect x="1000" y="625" width="614" height="53" fill="var(--orange)"/>
    <polygon role="img" aria-label="Photo of a polished white hatchback with a carbon bonnet in the detailing studio" points="991,187 1614,187 1614,625 991,625 855,405" fill="url(#photoWhiteCar)"/>
    <polygon points="1055,85 1085,132 1025,132" fill="var(--brown)"/>
    <polygon points="1055,727 1085,678 1025,678" fill="var(--brown)"/>
    <polygon points="985,85 1055,85 855,405 1055,727 985,727 785,405" fill="var(--yellow)"/>
    <polygon points="73,513 770,513 805,570 73,570" fill="var(--red)"/>

    <!-- stage two -->
    <rect x="73" y="743" width="1541" height="437" fill="var(--dark)"/>
    <rect x="73" y="688" width="617" height="55" fill="var(--orange)"/>
    <rect x="73" y="1180" width="617" height="53" fill="var(--orange)"/>
    <polygon role="img" aria-label="Photo close-up of a corrected silver car wing and headlight" points="73,743 698,743 833,962 698,1180 73,1180" fill="url(#photoSilverCar)"/>
    <polygon points="635,641 605,688 665,688" fill="var(--brown)"/>
    <polygon points="635,1283 605,1233 665,1233" fill="var(--brown)"/>
    <polygon points="635,641 705,641 903,962 705,1283 635,1283 833,962" fill="var(--yellow)"/>
    <polygon points="920,1068 1614,1068 1614,1125 882,1125" fill="var(--red)"/>

    <!-- stage three -->
    <rect x="73" y="1307" width="1541" height="490" fill="var(--dark)"/>
    <rect x="1000" y="1252" width="614" height="55" fill="var(--orange)"/>
    <rect x="1000" y="1745" width="614" height="52" fill="var(--orange)"/>
    <polygon role="img" aria-label="Photo of the mirror-finish rear of a black SUV after paint correction" points="991,1307 1614,1307 1614,1745 991,1745 855,1525" fill="url(#photoBlackCar)"/>
    <polygon points="1055,1205 1085,1252 1025,1252" fill="var(--brown)"/>
    <polygon points="1055,1847 1085,1797 1025,1797" fill="var(--brown)"/>
    <polygon points="985,1205 1055,1205 855,1525 1055,1847 985,1847 785,1525" fill="var(--yellow)"/>
    <polygon points="73,1700 770,1700 805,1757 73,1757" fill="var(--red)"/>

    <!-- footer band -->
    <polygon points="0,1906 940,1906 968,1955 1688,1955 1688,2184 0,2184" fill="var(--red)"/>
  </svg>

  <header class="abs brand">
    <div class="brand-name"><span class="brand-dot"></span>VELVORA SHINE</div>
    <div class="brand-tag">DETAILING, PAINT CORRECTION AND ENHANCEMENT</div>
  </header>

  <!-- Stage one -->
  <section>
    <h1 class="abs stage-title" style="left:60px;top:117px">STAGE ONE</h1>
    <p class="abs stage-copy" style="left:61px;top:157px">
      Ideally suited to Brand new or exceptionally<br>
      well-maintained vehicles. This Stage will remove light<br>
      swirl marks, marring and micro scratches typically<br>
      found in new car preparation or from home car washing<br>
      methods. It includes; full inspection and prewash,<br>
      wheels cleaned, snow foam, decontamination process,<br>
      single stage machine polish, glass cleaned and a Liquid<br>
      wax finish. This will give up to 6 months protection and<br>
      takes between 1 - 1.5 days.
    </p>
    <div class="abs prices-label" style="left:60px;top:291px">PRICES;</div>
    <div class="abs price-col" style="left:143px;top:286px">Small car ------- £240<br>Medium car --- £270</div>
    <div class="abs price-col" style="left:258px;top:286px">Large car ---------------------------£300<br>4x4s/pickups/vans from ---£350</div>
    <div class="abs footnote" style="left:137px;top:321px">*Upgrade to a hard wax finish with up to 12 months protection + interior valet from £130</div>
  </section>

  <!-- Stage two -->
  <section>
    <h1 class="abs stage-title right" style="right:62px;top:422px">STAGE TWO</h1>
    <p class="abs stage-copy right" style="right:64px;top:459px">
      This is our most popular package and will suit most<br>
      vehicles. It includes everything from stage 1 plus a<br>
      2-stage polish that will address light scratches and<br>
      imperfection, oxidation and begin to correct and level<br>
      the paint surface resulting in an exceptional shine.<br>
      Combined with a hard wax coating this will not only lock<br>
      in the shine for longer but also make home cleaning and<br>
      maintenance easier and more effective. This will give<br>
      6-9 months protection and takes from 2.5 days
    </p>
    <div class="abs prices-label" style="left:524px;top:595px">PRICES;</div>
    <div class="abs price-col" style="left:600px;top:590px">Small car ------- £400<br>Medium car --- £430</div>
    <div class="abs price-col" style="left:713px;top:590px">Large car ---------------------------£460<br>4x4s/pickups/vans from ---£500</div>
    <div class="abs footnote right" style="right:64px;top:627px">*Upgrade to a ceramic coating with 2 - 3 years protection + interior valet from £250</div>
  </section>

  <!-- Stage three -->
  <section>
    <h1 class="abs stage-title" style="left:60px;top:728px">STAGE THREE</h1>
    <p class="abs stage-copy" style="left:61px;top:765px">
      This is our luxury level paint correction. It includes<br>
      everything from stage 2 plus a 3 stage polish that will<br>
      provide a glorious, better than new, mirror like shine.<br>
      The 3 stage polish will remove medium to heavy<br>
      scratches and will level the paint to give that wet look<br>
      glossy finish you never thought possible. For the<br>
      ultimate protection we recommend taking advantage of<br>
      a professional grade ceramic coating which when<br>
      applied will lock in that glossy finish and provide the<br>
      longest possible protection. A full valet is included on<br>
      this stage and with basic hard wax your protection will<br>
      last up to 12 months and takes from 3.5 days.
    </p>
    <div class="abs prices-label" style="left:62px;top:943px">PRICES;</div>
    <div class="abs price-col" style="left:143px;top:937px">Small car ------- £600<br>Medium car --- £630</div>
    <div class="abs price-col" style="left:258px;top:937px">Large car ---------------------------£660<br>4x4s/pickups/vans from ---£700</div>
    <div class="abs footnote" style="left:144px;top:973px">*Interior valet included, add ceramic coating with 2 - 3 years protection from £200</div>
  </section>

  <!-- Footer -->
  <section class="abs upgrades">
    <h2>Upgrades available on all stages</h2>
    <ul class="upgrade-list">
      <li>Hard Carnauba Wax Protection; 1 year from<span class="lead"></span>£70</li>
      <li>Ceramic Coating; 2 -3 years paint protection from<span class="lead"></span>£200</li>
      <li>Ceramic Wheel Protection from<span class="lead"></span>£100</li>
      <li>Ceramic Leather protection from<span class="lead"></span>£100</li>
      <li>Glass protection from<span class="lead"></span>£40</li>
      <li>Interior valet; Full deep steam clean including Carpets, Mats,</li>
      <li>Leather cleaner, Plastics and sanitisation from<span class="lead"></span>£80</li>
    </ul>
  </section>

  <div class="abs footer-brand">
    <div class="brand-name"><span class="brand-dot"></span>VELVORA SHINE</div>
    <div class="brand-tag">DETAILING, PAINT CORRECTION AND ENHANCEMENT</div>
  </div>

  <div class="abs call-icon">
    <svg viewBox="0 0 24 24" width="30" height="30" aria-hidden="true">
      <path d="M7.2 4.5c.5-.3 1.1-.2 1.4.3l1.6 2.6c.3.5.2 1.1-.2 1.4l-1.2.9c.8 1.9 2.3 3.5 4.3 4.4l.9-1.2c.4-.4 1-.5 1.4-.2l2.6 1.6c.5.3.6.9.3 1.4l-.9 1.4c-.5.8-1.5 1.2-2.4.9C10.6 16.6 7.4 13.4 6 9c-.3-.9.1-1.9.9-2.4z" fill="#fff"/>
    </svg>
  </div>
  <div class="abs call-label">CALL OWEN</div>
  <div class="abs call-number">07700 900 482</div>

  <ul class="abs contact">
    <li><span class="ico">
      <svg viewBox="0 0 16 16" width="13" height="15" aria-hidden="true"><path d="M8 1a5 5 0 0 0-5 5c0 3.6 5 9 5 9s5-5.4 5-9a5 5 0 0 0-5-5zm0 7a2 2 0 1 1 0-4 2 2 0 0 1 0 4z" fill="var(--pin)"/></svg>
    </span>ALDER VALE, KESTOW KT9</li>
    <li><span class="ico"><span class="social-square"></span></span>VELVORA SHINE VEHICLE DETAILING</li>
    <li class="mail"><span class="ico">
      <svg viewBox="0 0 16 16" width="15" height="13" aria-hidden="true"><rect x="1" y="3" width="14" height="10" rx="1.5" fill="#fff"/><path d="M1.5 4l6.5 5 6.5-5" stroke="var(--red)" stroke-width="1.3" fill="none"/></svg>
    </span>hello@velvorashine.uk</li>
  </ul>

</main>
</body>
</html>
```